Stationery Design Project

I need a stationary design for our company. we are based in Houston, TX and we are called Mira Vell Lending. And we are wanting to brand our MoneyMendPlus program, which includes our tax preparation and restoration, credit repair service. Although our business offers other programs, we are interested in mainly focusing on The MoneyMendPlus program. We are looking for way to brand our ourselves and I believe that a great stationery design will help in achieving this goal. Our logo design is blue and light blue. the slogan is orange.

Industry/Entity Type

Business

Requirements
Must have
• Address: 30871 Calloway Ln. B-22
Houston, TX 75419
Tel. 555-318-6207
Fax 555-294-7153
www.miravelllending.example
info@miravelllending.example
Our Slogan: Happiness, Restored!

```html
<!DOCTYPE html>
<html lang="en">
<head>
<meta charset="utf-8">
<title>Mira Vell Lending – Business Cards</title>
<link rel="stylesheet" href="https://fonts.googleapis.com/css2?family=Cinzel:wght@500&family=Open+Sans:wght@400&family=Tinos&display=swap">
<style>
  :root {
    --backdrop: #ece7e1;
    --card-white: #ffffff;
    --navy: #0f3d66;
    --brand-blue: #1d5a92;
    --pale-blue: #cfe3f3;
    --slogan-orange: #f0962c;
    --ink: #2f2f2f;
    --faint-grey: #c5c8d4;
    --faint-text: #eef0f5;
  }
  * { margin: 0; padding: 0; box-sizing: border-box; }
  html, body { width: 1200px; height: 788px; overflow: hidden; }
  body { background: var(--backdrop); position: relative; font-family: "Open Sans", sans-serif; }

  .view-label {
    position: absolute; width: 300px; text-align: center;
    font-size: 20px; color: #111; font-family: "Open Sans", sans-serif;
  }
  .card {
    position: absolute; width: 525px; height: 300px;
    border-radius: 22px; background: var(--card-white); overflow: hidden;
  }
  .card--navy { background: var(--navy); }

  .slogan {
    position: absolute; left: 0; width: 100%; text-align: center;
    font-family: "Cinzel", serif; font-weight: 500; font-size: 29px;
    color: var(--slogan-orange); letter-spacing: 0.5px;
  }

  /* front */
  .program-name {
    position: absolute; left: 30px; top: 100px;
    font-family: "Tinos", serif; font-size: 46px; color: var(--brand-blue);
  }
  .address {
    position: absolute; left: 29px; top: 234px;
    font-size: 13.5px; line-height: 18px; color: var(--ink);
  }
  .contact-list {
    position: absolute; left: 309px; top: 196px; list-style: none;
    font-size: 12.8px; line-height: 18px; color: var(--ink);
  }
  .contact-list li { display: flex; align-items: center; gap: 6px; }
  .contact-list svg { width: 11px; height: 11px; flex: none; }

  /* company mark */
  .company-mark {
    position: absolute; left: 50%; transform: translateX(-50%);
    display: flex; flex-direction: column; align-items: center; gap: 14px;
  }
  .company-mark .mark-square { width: 64px; height: 64px; background: var(--navy); }
  .company-mark .company-name { font-family: "Tinos", serif; font-size: 17px; color: var(--navy); white-space: nowrap; }
  .company-mark--faint .mark-square { background: var(--faint-grey); }
  .company-mark--faint .company-name { color: var(--faint-grey); }
  .company-mark--light .mark-square { background: var(--pale-blue); }
  .company-mark--light .company-name { color: #fff; }

  .web-address {
    position: absolute; left: 0; width: 100%; text-align: center; top: 258px;
    font-size: 19px; letter-spacing: 2px; color: #111;
  }
</style>
</head>
<body>
  <div class="view-label" style="left:167px; top:33px;">Front</div>
  <div class="view-label" style="left:746px; top:33px;">Back - 1</div>
  <div class="view-label" style="left:174px; top:404px;">Back - 2</div>
  <div class="view-label" style="left:746px; top:404px;">Back - 3</div>

  <section class="card card--front" style="left:54px; top:74px;">
    <div class="program-name">MoneyMendPlus</div>
    <p class="address">30871 Calloway Ln. B-22<br>Houston, TX 75419</p>
    <ul class="contact-list">
      <li><svg viewBox="0 0 12 12"><path d="M3 1l2 2.5-1.2 1.3a7 7 0 0 0 3.4 3.4L8.5 7 11 9l-1.3 1.8C5.5 10.5 1.5 6.5 1.2 2.3z" fill="#333"/></svg>555-318-6207</li>
      <li><svg viewBox="0 0 12 12"><rect x="3" y="1" width="6" height="4" fill="none" stroke="#333"/><rect x="1" y="5" width="10" height="5" rx="1" fill="#333"/></svg>555-294-7153</li>
      <li><svg viewBox="0 0 12 12"><rect x="1" y="3" width="10" height="7" fill="none" stroke="#333"/><path d="M1 3l5 4 5-4" fill="none" stroke="#333"/></svg>info@miravelllending.example</li>
      <li><svg viewBox="0 0 12 12"><circle cx="6" cy="6" r="5" fill="none" stroke="#333"/><path d="M1 6h10M6 1c-3 3-3 7 0 10M6 1c3 3 3 7 0 10" fill="none" stroke="#333" stroke-width=".8"/></svg>www.miravelllending.example</li>
    </ul>
  </section>

  <section class="card card--back-one" style="left:622px; top:74px;">
    <div class="company-mark" style="top:62px;">
      <div class="mark-square"></div>
      <div class="company-name">Mira Vell Lending</div>
    </div>
    <p class="slogan" style="top:230px;">Happiness, Restored!</p>
  </section>

  <section class="card card--back-two" style="left:58px; top:445px;">
    <p class="slogan" style="top:16px;">Happiness, Restored!</p>
    <div class="company-mark company-mark--faint" style="top:92px;">
      <div class="mark-square"></div>
      <div class="company-name">Mira Vell Lending</div>
    </div>
    <p class="web-address">www.miravelllending.example</p>
  </section>

  <section class="card card--navy card--back-three" style="left:622px; top:445px;">
    <div class="company-mark company-mark--light" style="top:70px;">
      <div class="mark-square"></div>
      <div class="company-name">Mira Vell Lending</div>
    </div>
    <p class="slogan" style="top:242px;">Happiness, Restored!</p>
  </section>
</body>
</html>
```